13 Varno - new website design project

Our company Varno Electrical is developing a new lead generation website focused on Electrical, LED Lighting and Solar Power. We need a high converting website.

Example of our current website is www.varnoelectrical-example.com.au You can take content from this website for this new design. Our colours are red, black and white. For our new website we would like to promote Varno, Spark Every Day. Please listen to the jingle.

The below link is the company jingle that we have developed.
http://www.tunecraftdemo.com.au/vrn-tc-v1/

The key for this brief is to generate leads for Electrical, LED Lighting (for commercial) and Solar Power & Storage.

Target Market(s)

Business owners in Melbourne Victoria

Number of Pages Required

4 page

Colors
ec1f27
ffffff

Requirements
Must have
• This page must be clean, be in line with company branding and a high converting lead website.

```html
<!DOCTYPE html>
<html lang="en">
<head>
<meta charset="utf-8">
<title>Varno Electrical</title>
<link href="https://fonts.googleapis.com/css2?family=Exo+2:wght@500;600;700;800&family=Lato:wght@400;700&display=swap" rel="stylesheet">
<style>
:root{
  --red:#e0161f;
  --red-dark:#b8141b;
  --ink:#222;
  --text:#555;
  --muted:#888;
  --line:#dcdcdc;
  --navy:#142139;
  --navy-2:#22324f;
  --paper:#f5f5f5;
  --white:#fff;
  --footer:#1c1c1c;
}
*{box-sizing:border-box;margin:0;padding:0}
html,body{width:1200px;height:3333px;overflow:hidden}
body{position:relative;background:var(--white);font-family:"Lato",Arial,sans-serif;color:var(--text)}
.abs{position:absolute}
.heading{font-family:"Exo 2",Arial,sans-serif;font-weight:800;font-size:32px;color:var(--ink);text-transform:uppercase;text-align:center;letter-spacing:.5px}
.heading span{color:var(--red)}
.divider{display:block;margin:10px auto 0;width:24px;height:24px}
.btn{display:inline-flex;align-items:center;gap:6px;font-family:"Lato",sans-serif;font-weight:700;font-size:14px;color:#fff}
.btn b{background:var(--red);padding:8px 16px;border-radius:3px;font-weight:700}
.btn i{width:22px;height:22px;border:2px solid var(--red);border-radius:50%;display:block}

/* header */
.header{top:0;left:0;width:1200px;height:130px;background:#fff}
.brand{left:100px;top:18px}
.brand-name{font-family:"Exo 2",sans-serif;font-weight:800;font-size:52px;color:var(--red);line-height:1;display:flex;align-items:center;gap:12px}
.brand-name i{width:40px;height:40px;background:var(--red);border-radius:50%;display:block}
.brand-tag{font-family:"Exo 2",sans-serif;font-weight:600;font-size:17px;color:var(--ink);margin-top:4px;margin-left:52px}
.topbar{top:22px;right:98px;display:flex;align-items:center;gap:16px;font-size:15px;color:var(--ink)}
.topbar .ico{width:30px;height:30px;border-radius:50%;background:var(--ink);display:inline-flex;align-items:center;justify-content:center;margin-right:8px;vertical-align:middle}
.topbar .sep{width:1px;height:30px;background:var(--line)}
.social{display:flex;gap:8px}
.social i{width:30px;height:30px;border-radius:50%;background:var(--ink);display:block}
.nav{top:78px;left:350px;width:850px;height:52px;background:var(--red);display:flex;font-family:"Exo 2",sans-serif;font-weight:600;font-size:15px;color:#fff;text-transform:uppercase}
.nav a{display:flex;align-items:center;justify-content:center;border-right:1px solid rgba(255,255,255,.3);color:#fff;text-decoration:none}
.nav .home{width:95px;text-decoration:underline;text-underline-offset:6px}
.nav .w{width:145px}
.nav .book{flex:1;background:var(--red-dark);font-size:17px;border:none}

/* hero */
.hero{top:130px;left:0;width:1200px;height:515px;background:linear-gradient(180deg,#7c8694 0%,#5b6574 55%,#2d3440 100%)}
.hero-circle{border-radius:50%;border:6px solid rgba(255,255,255,.85);background:linear-gradient(160deg,#8b9ab0,#3c4a60)}
.hero-arrow{top:225px;width:20px;height:40px}
.hero-title{top:442px;width:1200px;text-align:center;font-family:"Exo 2",sans-serif;font-weight:700;font-size:26px;color:#fff;text-shadow:0 2px 4px rgba(0,0,0,.5);letter-spacing:.4px}

/* about */
.about{top:645px;left:0;width:1200px;height:375px}
.about .heading{margin-top:42px}
.about p{width:1000px;margin:0 auto;text-align:center;font-size:12.5px;line-height:22px;color:var(--text)}
.about p.lead{margin-top:26px;color:#444}
.about p+p{margin-top:6px}
.about .btn{position:absolute;left:537px;top:290px}

/* services */
.services{top:1020px;left:0;width:1200px;height:670px;background:linear-gradient(180deg,#1a2840 0%,#111c30 60%,#0f1a2c 100%)}
.services .heading{color:#fff;margin-top:44px}
.card{top:140px;width:308px;height:405px;background:#fff;border-radius:3px;padding:8px}
.card h3{background:var(--red);color:#fff;font-family:"Exo 2",sans-serif;font-weight:700;font-size:17px;text-align:center;height:42px;line-height:42px;text-transform:uppercase;letter-spacing:.3px}
.card .photo{height:190px;margin-top:10px;background:linear-gradient(160deg,#b9c1cc,#6d7785)}
.card p{text-align:center;font-size:12.5px;line-height:19px;color:#444;margin-top:14px;padding:0 12px}
.card .btn{margin-top:10px;justify-content:center;width:100%}
.services .all{position:absolute;left:493px;top:590px}

/* work */
.work{top:1690px;left:0;width:1200px;height:628px;background:#fff}
.work .heading{margin-top:38px}
.tile{width:316px;height:206px}
.tile .logo{height:68px;background:#fff;display:flex;align-items:center;justify-content:center;font-family:"Exo 2",sans-serif;font-weight:800;font-size:30px;color:var(--ink)}
.tile .shot{height:138px;background:linear-gradient(180deg,#9aa3ad,#5e6670)}
.tile .zoom{position:absolute;right:10px;bottom:10px;width:36px;height:36px}
.tile.feature{background:#2a2a2a;color:#fff;text-align:center;padding:18px 26px}
.tile.feature h4{font-family:"Exo 2",sans-serif;font-size:18px;font-weight:700}
.tile.feature small{display:block;font-size:12px;color:#ddd;margin-top:2px}
.tile.feature p{font-size:13px;line-height:19px;margin-top:10px}
.tile.brandtile{background:#ececec;display:flex;align-items:center;justify-content:center;font-family:"Exo 2",sans-serif;font-weight:800;font-size:60px;color:var(--red);gap:14px}
.tile.brandtile i{width:44px;height:44px;border-radius:50%;background:var(--red);display:block}

/* why + testimonials */
.why{top:2318px;left:0;width:1200px;height:542px;background:#fff;border-top:1px solid #eee}
.col-title{font-family:"Exo 2",sans-serif;font-weight:800;font-size:28px;color:var(--ink);text-transform:uppercase}
.col-title span{color:var(--red)}
.rule{height:1px;background:var(--line);margin-top:12px}
.acc{left:100px;width:472px}
.acc-item{position:absolute;left:0;width:472px;height:44px;border:1px solid var(--line);background:#fff;display:flex;align-items:center;font-family:"Exo 2",sans-serif;font-weight:600;font-size:14px;color:var(--ink);text-transform:uppercase}
.acc-item .pm{width:42px;height:42px;background:var(--red);display:flex;align-items:center;justify-content:center;margin-right:14px}
.acc-body{position:absolute;left:0;width:472px;background:#f3f3f3;border:1px solid var(--line);border-top:none;padding:10px 14px;font-size:12.5px;line-height:19px;color:#444}
.col-sep{left:600px;top:2345px;width:1px;height:480px;background:var(--line)}
.testi{left:635px;width:465px}
.testi .photo{height:180px;background:linear-gradient(180deg,#9eb4c9 0%,#cdd6df 45%,#8c8c8c 100%)}
.testi blockquote{font-size:13.5px;line-height:21px;color:#444;text-align:center;margin-top:16px;padding:0 4px}
.testi .who{text-align:center;margin-top:18px;font-family:"Exo 2",sans-serif;font-weight:700;font-size:17px;color:var(--ink)}
.testi .role{text-align:center;font-size:12px;color:#444;font-weight:700}
.dots{display:flex;justify-content:center;gap:8px;margin-top:20px}
.dots i{width:11px;height:11px;border-radius:50%;background:#555;display:block}
.dots i.on{background:var(--red)}

/* contact */
.contact{top:2860px;left:0;width:1200px;height:368px;background:var(--paper)}
.contact .heading{margin-top:42px}
.contact .intro{width:1000px;margin:22px auto 0;text-align:center;font-size:12.5px;line-height:22px;color:#555}
.field{position:absolute;height:30px;background:#fff;border:1px solid var(--line);font-size:11.5px;color:#666;padding:8px 6px}
.submit{position:absolute;left:108px;top:305px}
.info{left:865px;top:185px;font-size:12.5px;line-height:19px;color:#555}
.info div{display:flex;gap:16px;margin-bottom:10px}
.info svg{flex:none;margin-top:2px}

/* footer */
.foot-nav{top:3228px;left:0;width:1200px;height:62px;background:var(--red);display:flex;justify-content:center;align-items:center;font-family:"Exo 2",sans-serif;font-weight:600;font-size:14px;color:#fff;text-transform:uppercase}
.foot-nav a{color:#fff;text-decoration:none;padding:0 42px;border-right:1px solid rgba(255,255,255,.4)}
.foot-nav a:last-child{border:none}
.foot-bar{top:3290px;left:0;width:1200px;height:43px;background:var(--footer);color:#ddd;font-size:12px}
.foot-bar .copy{position:absolute;left:100px;top:14px}
.foot-bar .social{position:absolute;right:98px;top:7px}
.foot-bar .social i{background:#fff;width:28px;height:28px}
</style>
</head>
<body>

<header class="header abs">
  <div class="brand abs">
    <div class="brand-name"><i></i>Varno</div>
    <div class="brand-tag">Spark Every Day</div>
  </div>
  <div class="topbar abs">
    <span><span class="ico"><svg width="14" height="14" viewBox="0 0 24 24"><path fill="#fff" d="M6.6 10.8a15 15 0 006.6 6.6l2.2-2.2a1 1 0 011-.25 11.4 11.4 0 003.6.57 1 1 0 011 1V20a1 1 0 01-1 1A17 17 0 013 4a1 1 0 011-1h3.5a1 1 0 011 1c0 1.25.2 2.45.57 3.57a1 1 0 01-.25 1z"/></svg></span>139654</span>
    <span><span class="ico"><svg width="14" height="14" viewBox="0 0 24 24"><path fill="#fff" d="M2 5h20v14H2z"/><path d="M2 5l10 8 10-8" stroke="#222" stroke-width="2" fill="none"/></svg></span>service@varnoelectrical-example.com.au</span>
    <span class="sep"></span>
    <span class="social"><i></i><i></i><i></i></span>
  </div>
  <nav class="nav abs">
    <a class="home">Home</a><a class="w">About Us</a><a class="w" style="width:170px">Our Service</a><a class="w" style="width:160px">Contact Us</a><a class="book">Book Online</a>
  </nav>
</header>

<section class="hero abs">
  <div class="hero-circle abs" role="img" aria-label="Warehouse lighting photo" style="left:275px;top:120px;width:170px;height:170px;opacity:.85"></div>
  <div class="hero-circle abs" role="img" aria-label="Technicians installing solar panels on a roof" style="left:735px;top:120px;width:170px;height:170px;opacity:.85"></div>
  <div class="hero-circle abs" role="img" aria-label="Electrician in hard hat holding cable" style="left:430px;top:25px;width:330px;height:330px;background:linear-gradient(160deg,#b8c2cf,#2f3c55)"></div>
  <svg class="hero-arrow abs" style="left:242px" viewBox="0 0 20 40"><path d="M16 4L4 20l12 16" stroke="#fff" stroke-width="3" fill="none"/></svg>
  <svg class="hero-arrow abs" style="left:940px" viewBox="0 0 20 40"><path d="M4 4l12 16L4 36" stroke="#fff" stroke-width="3" fill="none"/></svg>
  <h1 class="hero-title abs">Australia's Largest Fully Integrated Electrical &amp; Energy Solutions Provider.</h1>
</section>

<section class="about abs">
  <h2 class="heading">About <span>Us</span></h2>
  <svg class="divider" viewBox="0 0 24 24"><circle cx="12" cy="12" r="8" fill="none" stroke="#ccc" stroke-width="2"/></svg>
  <p class="lead">Varno Electrical was formed to be an expert Electricity Contracting Company providing services to all Residential and Commercial Customers. With over 10 years of experience, Varno Electrical has developed a highly-experienced team of professionals that ensure all our customer expectations are met.</p>
  <p>Electrical and Energy Solutions are at the forefront of our company. Varno Electrical has a long history in Electrical, LED Lighting and Solar Power and just like the spark in our name, we will strive to be fierce &amp; agile in an effort to exceed our customer's expectations and develop stronger links with all our business partners &amp; community. Varno Electrical is an expert Electrical Company providing services to all Residential and Commercial customers. With over 10 years of experience, Varno Electrical has developed a highly-experienced team of professionals that ensure all our customer expectations are exceeded.</p>
  <span class="btn"><b>Read More</b><i></i></span>
</section>

<section class="services abs">
  <h2 class="heading">Our Service</h2>
  <svg class="divider" viewBox="0 0 24 24"><circle cx="12" cy="12" r="8" fill="none" stroke="#667" stroke-width="2"/></svg>
  <div class="card abs" style="left:100px">
    <h3>Electrical Contracting</h3>
    <div class="photo" role="img" aria-label="Hands stripping wires at a switchboard"></div>
    <p>Lorem ipsum dolor sit amet, consectetuer adipiscing elit, sed diam nonummy nibh euismod tincidunt ut laoreet dolore maex</p>
    <span class="btn"><b>Read More</b><i></i></span>
  </div>
  <div class="card abs" style="left:446px">
    <h3>LED Lighting Upgrades</h3>
    <div class="photo" role="img" aria-label="Bright warehouse with LED ceiling lights" style="background:linear-gradient(180deg,#e8ecf0,#9aa4ae)"></div>
    <p>Lorem ipsum dolor sit amet, consectetuer adipiscing elit, sed diam nonummy nibh euismod tincidunt ut laoreet dolore maex</p>
    <span class="btn"><b>Read More</b><i></i></span>
  </div>
  <div class="card abs" style="left:792px">
    <h3>Solar Power</h3>
    <div class="photo" role="img" aria-label="Workers fitting solar panels on a roof" style="background:linear-gradient(160deg,#3f6fb3,#1d3a73 60%,#5f8a3a)"></div>
    <p>Lorem ipsum dolor sit amet, consectetuer adipiscing elit, sed diam nonummy nibh euismod tincidunt ut laoreet dolore maex</p>
    <span class="btn"><b>Read More</b><i></i></span>
  </div>
  <span class="btn all"><b>View All Other Services</b><i></i></span>
</section>

<section class="work abs">
  <h2 class="heading">Our <span>Work</span></h2>
  <svg class="divider" viewBox="0 0 24 24"><circle cx="12" cy="12" r="8" fill="none" stroke="#ccc" stroke-width="2"/></svg>
  <div class="tile feature abs" style="left:100px;top:135px">
    <h4>D. Morrell</h4><small>Ashvale North, VIC</small>
    <p>They clean up after the job, explained everything I needed to know and answered all questions, very professional. I was very happy. Will use them again in the future!</p>
  </div>
  <div class="tile abs" style="left:442px;top:135px">
    <div class="logo" style="background:#f5d90a">Outback Supply Co</div>
    <div class="shot" role="img" aria-label="Retail warehouse interior with lighting"></div>
    <svg class="zoom" viewBox="0 0 36 36"><circle cx="18" cy="18" r="17" fill="#fff"/><circle cx="16" cy="16" r="7" fill="none" stroke="#333" stroke-width="2.5"/><path d="M21 21l7 7M13 16h6M16 13v6" stroke="#333" stroke-width="2.5"/></svg>
  </div>
  <div class="tile abs" style="left:785px;top:135px">
    <div class="logo">Plasterline</div>
    <div class="shot" role="img" aria-label="Building facade of a plaster supplier" style="background:linear-gradient(180deg,#b3c6d8,#d4d8dc 50%,#8e2a2a)"></div>
    <svg class="zoom" viewBox="0 0 36 36"><circle cx="18" cy="18" r="17" fill="#fff"/><circle cx="16" cy="16" r="7" fill="none" stroke="#333" stroke-width="2.5"/><path d="M21 21l7 7M13 16h6M16 13v6" stroke="#333" stroke-width="2.5"/></svg>
  </div>
  <div class="tile abs" style="left:100px;top:367px">
    <div class="logo">Harwick Signs</div>
    <div class="shot" role="img" aria-label="Sign workshop with overhead lights"></div>
    <svg class="zoom" viewBox="0 0 36 36"><circle cx="18" cy="18" r="17" fill="#fff"/><circle cx="16" cy="16" r="7" fill="none" stroke="#333" stroke-width="2.5"/><path d="M21 21l7 7M13 16h6M16 13v6" stroke="#333" stroke-width="2.5"/></svg>
  </div>
  <div class="tile abs" style="left:442px;top:367px">
    <div class="logo" style="color:#1f6fb3">Steelmark</div>
    <div class="shot" role="img" aria-label="Steel storage warehouse interior"></div>
    <svg class="zoom" viewBox="0 0 36 36"><circle cx="18" cy="18" r="17" fill="#fff"/><circle cx="16" cy="16" r="7" fill="none" stroke="#333" stroke-width="2.5"/><path d="M21 21l7 7M13 16h6M16 13v6" stroke="#333" stroke-width="2.5"/></svg>
  </div>
  <div class="tile brandtile abs" style="left:785px;top:367px"><i></i>Varno</div>
</section>

<section class="why abs">
  <div class="abs" style="left:100px;top:55px;width:472px">
    <h2 class="col-title">Why <span>Choose Us?</span></h2>
    <div class="rule"></div>
  </div>
  <div class="acc abs" style="top:125px">
    <div class="acc-item" style="top:0"><span class="pm"><svg width="16" height="16"><path d="M8 1v14M1 8h14" stroke="#fff" stroke-width="3"/></svg></span>Professional Service</div>
    <div class="acc-item" style="top:58px"><span class="pm"><svg width="16" height="16"><path d="M1 8h14" stroke="#fff" stroke-width="3"/></svg></span>5 Year Workmanship Guarantee</div>
    <div class="acc-body" style="top:102px">You can buy with confidence as all of our work has a 5 year workmanship guarantee. For your peace of mind, we unconditionally back our electrical work. We will come back to fix any problems at our own expense.</div>
    <div class="acc-item" style="top:190px"><span class="pm"><svg width="16" height="16"><path d="M8 1v14M1 8h14" stroke="#fff" stroke-width="3"/></svg></span>Value For Money</div>
    <div class="acc-item" style="top:250px"><span class="pm"><svg width="16" height="16"><path d="M8 1v14M1 8h14" stroke="#fff" stroke-width="3"/></svg></span>Environmentally Friendly</div>
    <div class="acc-item" style="top:310px"><span class="pm"><svg width="16" height="16"><path d="M8 1v14M1 8h14" stroke="#fff" stroke-width="3"/></svg></span>Fully Insured</div>
  </div>
  <div class="testi abs" style="top:55px">
    <h2 class="col-title">Clients <span>Testimonials</span></h2>
    <div class="rule" style="margin-bottom:12px"></div>
    <div class="photo" role="img" aria-label="Client building exterior with signage"></div>
    <blockquote>“ Varno Electrical was pleasantly efficient, cost effective and delivered the desired results we were after. we look forward to seeing an ongoing benefit from dealing with them when we pay the Electrical bill going forward.”</blockquote>
    <div class="who">- Glen Ashcroft</div>
    <div class="role">General Manager Plasterline</div>
    <div class="dots"><i class="on"></i><i></i><i></i><i></i></div>
  </div>
</section>
<div class="col-sep abs"></div>

<section class="contact abs">
  <h2 class="heading">Keep <span>In Touch</span></h2>
  <p class="intro">Lorem Ipsum is simply dummy text of the printing and typesetting industry. Lorem Ipsum has been the industry's standard dummy text ever since the 1500s, when an unknown printer took a galley of type and scrambled it to make a type specimen book.</p>
  <div class="field" style="left:108px;top:190px;width:232px">Your Name</div>
  <div class="field" style="left:350px;top:190px;width:232px">Your Email</div>
  <div class="field" style="left:592px;top:190px;width:232px">Your Subject</div>
  <div class="field" style="left:108px;top:225px;width:716px;height:68px">Message</div>
  <span class="btn submit"><b>Submit</b><i></i></span>
  <div class="info abs">
    <div><svg width="14" height="16" viewBox="0 0 14 16"><path d="M7 0a6 6 0 016 6c0 4-6 10-6 10S1 10 1 6a6 6 0 016-6z" fill="#444"/><circle cx="7" cy="6" r="2" fill="#fff"/></svg><span>12/48 Calder Rd<br>Glenwood<br>VIC 3190</span></div>
    <div><svg width="14" height="14" viewBox="0 0 24 24"><path fill="#444" d="M6.6 10.8a15 15 0 006.6 6.6l2.2-2.2a1 1 0 011-.25 11.4 11.4 0 003.6.57 1 1 0 011 1V20a1 1 0 01-1 1A17 17 0 013 4a1 1 0 011-1h3.5a1 1 0 011 1c0 1.25.2 2.45.57 3.57a1 1 0 01-.25 1z"/></svg><span>139654</span></div>
    <div><svg width="14" height="14" viewBox="0 0 14 14"><rect x="1" y="2" width="12" height="10" rx="1" fill="#444"/><rect x="3" y="4" width="8" height="3" fill="#fff"/></svg><span>(03) 555 - 0182</span></div>
    <div><svg width="14" height="14" viewBox="0 0 24 24"><path fill="#444" d="M2 5h20v14H2z"/><path d="M2 5l10 8 10-8" stroke="#fff" stroke-width="2" fill="none"/></svg><span>service@varnoelectrical-example.com.au</span></div>
  </div>
</section>

<nav class="foot-nav abs"><a>Home</a><a>About Us</a><a>Our Service</a><a>Contact Us</a></nav>
<footer class="foot-bar abs">
  <span class="copy">© 2017 Varno Electrical. All Rights Reserved.</span>
  <span class="social"><i></i><i></i><i></i></span>
</footer>

</body>
</html>
```